Quorva - corporate Business Card

We need a good look and innovative business card for a new start up company based in Los Angeles called "Quorva". We are in a payment business, including payment card, app, and ewallet. We are expert in online payment and Card not present (CNP) transaction.
We need an innovative, modern business card.

Our logo font is Aero Matics

Target Market(s)

Startup - Bank - Online Payment - Card Manufacturing

Industry/Entity Type

Startup

Contact Information for Business Card

phone: 555 014 7396 - Address: 4172 Marlowe Avenue, Fairbrook, NV 89031

Requirements
Must have
• Message: innovative, professional, expert, high tech, trust, online payment expert, security
Nice to have
• no comment
Should not have
• no Comment

```html
<!DOCTYPE html>
<html lang="en">
<head>
<meta charset="utf-8">
<title>Quorva – Business Card</title>
<link rel="stylesheet" href="https://fonts.googleapis.com/css2?family=Roboto:wght@400;500;700&display=swap">
<style>
  :root {
    --brand-red: #b81f30;
    --paper: #ffffff;
    --silver: #9a9c9e;
    --ink: #2b2b2b;
    --backdrop: #5f686d;
  }
  * { box-sizing: border-box; margin: 0; padding: 0; }
  html, body { width: 1200px; height: 900px; overflow: hidden; }
  body {
    background: var(--backdrop);
    font-family: "Roboto", Arial, sans-serif;
    position: relative;
  }
  .card {
    position: absolute;
    left: 250px;
    width: 700px;
    height: 400px;
    background: var(--paper);
    overflow: hidden;
    box-shadow: 0 10px 28px rgba(0,0,0,.35);
  }
  .card--front { top: 40px; }
  .card--back { top: 465px; }
  .card__waves { position: absolute; inset: 0; width: 100%; height: 100%; }

  .brand {
    position: absolute;
    display: flex;
    align-items: center;
    color: var(--brand-red);
    font-weight: 700;
  }
  .brand__dot { border-radius: 50%; background: var(--brand-red); }
  .card--front .brand { left: 44px; top: 42px; gap: 12px; font-size: 52px; }
  .card--front .brand__dot { width: 60px; height: 60px; }
  .card--back .brand { left: 50%; top: 120px; transform: translateX(-50%); gap: 18px; font-size: 92px; }
  .card--back .brand__dot { width: 100px; height: 100px; }

  .person { position: absolute; right: 40px; top: 140px; text-align: right; }
  .person__name { color: var(--brand-red); font-size: 22px; font-weight: 500; letter-spacing: .5px; }
  .person__name strong { font-weight: 700; }
  .person__role { color: var(--ink); font-size: 17px; letter-spacing: 1px; margin-top: 2px; }

  .contact { position: absolute; right: 36px; top: 252px; list-style: none; color: var(--paper); font-size: 15px; line-height: 21px; text-align: right; }
  .contact__item { display: flex; justify-content: flex-end; align-items: center; gap: 8px; }
  .contact__item--address { display: block; padding-right: 22px; margin-bottom: 4px; }
  .contact__icon { width: 14px; height: 14px; flex: none; }

  .web { position: absolute; left: 34px; bottom: 26px; color: var(--paper); font-size: 15px; }
</style>
</head>
<body>

<section class="card card--front" aria-label="Business card front">
  <svg class="card__waves" viewBox="0 0 700 400" aria-hidden="true">
    <path d="M0,96 C110,100 150,200 330,206 C480,212 580,216 700,222 L700,400 L0,400 Z" fill="var(--silver)"/>
    <path d="M0,104 C110,108 150,208 330,214 C480,220 580,224 700,230 L700,400 L0,400 Z" fill="var(--brand-red)"/>
    <path d="M10,118 C90,160 150,222 320,232 C430,238 480,240 560,242" fill="none" stroke="var(--silver)" stroke-width="2"/>
    <path d="M20,124 C100,170 150,222 260,236" fill="none" stroke="var(--paper)" stroke-width="2.5"/>
  </svg>

  <div class="brand"><span class="brand__dot"></span><span class="brand__name">quorva</span></div>

  <div class="person">
    <p class="person__name"><strong>DARREN</strong> HOLLOWAY</p>
    <p class="person__role">DESIGNER</p>
  </div>

  <ul class="contact">
    <li class="contact__item contact__item--address">4172 Marlowe Avenue<br>Fairbrook, NV 89031</li>
    <li class="contact__item">555 014 7396
      <svg class="contact__icon" viewBox="0 0 16 16"><path d="M4 1l3 3-2 2c1 2 3 4 5 5l2-2 3 3-2 3C7 15 1 9 1 3z" fill="currentColor"/></svg></li>
    <li class="contact__item">555.018.2264
      <svg class="contact__icon" viewBox="0 0 16 16"><rect x="4" y="1" width="8" height="14" rx="1.5" fill="none" stroke="currentColor" stroke-width="1.6"/></svg></li>
    <li class="contact__item">darren@quorvapay.com
      <svg class="contact__icon" viewBox="0 0 16 16"><rect x="1" y="3" width="14" height="10" fill="currentColor"/><path d="M1 3l7 6 7-6" fill="none" stroke="var(--brand-red)" stroke-width="1.4"/></svg></li>
    <li class="contact__item">www.quorvapay.com
      <svg class="contact__icon" viewBox="0 0 16 16"><circle cx="8" cy="8" r="6.5" fill="none" stroke="currentColor" stroke-width="1.6"/><path d="M1.5 8h13M8 1.5c-3 3-3 10 0 13M8 1.5c3 3 3 10 0 13" fill="none" stroke="currentColor" stroke-width="1.1"/></svg></li>
  </ul>
</section>

<section class="card card--back" aria-label="Business card back">
  <svg class="card__waves" viewBox="0 0 700 400" aria-hidden="true">
    <path d="M0,262 C140,258 260,320 420,352 C530,374 620,384 700,388 L700,400 L0,400 Z" fill="var(--silver)"/>
    <path d="M0,270 C140,266 260,328 420,360 C530,380 620,390 700,394 L700,400 L0,400 Z" fill="var(--brand-red)"/>
    <path d="M30,300 C180,300 300,362 470,386" fill="none" stroke="var(--silver)" stroke-width="2"/>
    <path d="M360,352 C460,374 560,386 680,396" fill="none" stroke="var(--paper)" stroke-width="2.5"/>
  </svg>

  <div class="brand"><span class="brand__dot"></span><span class="brand__name">quorva</span></div>

  <p class="web">www.quorvapay.com</p>
</section>

</body>
</html>
```